Varnex Consulting Business card design.

See our website www.varnexconsulting.example which will give you a good idea of what we are about. The font is called 'Play'.

I'd like a standout business card in keeping with the themes and branding on the website

Target Market(s)

professionals. HR directors

Industry/Entity Type

Business

Contact Information for Business Card

Varnex Consulting PO Box 3172 Merrowdale NSW 2291 1300 485 193 Gavin Threlkeld Principal email: career@varnexconsulting.example ABN: 71203948865

Font styles to use
Other font styles liked:
• Play

Requirements
Must have
• Must have same design colours and branding as website.
• On back I'd prefer a list of the things we do which appears below the name at the header on the website

```html
<!DOCTYPE html>
<html lang="en">
<head>
<meta charset="utf-8">
<title>Varnex Consulting – Business Card</title>
<link href="https://fonts.googleapis.com/css2?family=Play:wght@400;700&display=swap" rel="stylesheet">
<style>
  :root {
    --navy: #27324a;
    --navy-band: #2f3b56;
    --sky: #7fb3e0;
    --sky-soft: #9cc3e6;
    --white: #f3f5f8;
    --muted: #c9d2df;
    --stage: #e7e9ed;
  }
  * { box-sizing: border-box; margin: 0; padding: 0; }
  html, body { width: 1200px; height: 892px; overflow: hidden; }
  body {
    background: var(--stage);
    font-family: 'Play', sans-serif;
    display: flex;
    align-items: center;
    justify-content: center;
    gap: 100px;
  }
  .card {
    width: 400px;
    height: 700px;
    position: relative;
    overflow: hidden;
    background: var(--navy);
    box-shadow: 0 6px 20px rgba(0,0,0,.18);
  }
  .brand {
    font-size: 30px;
    font-weight: 400;
    letter-spacing: 1px;
    color: var(--white);
    white-space: nowrap;
    line-height: 1;
  }
  .services {
    font-size: 10.5px;
    letter-spacing: .9px;
    color: var(--sky-soft);
    margin-top: 12px;
    white-space: nowrap;
  }
  /* front */
  .front .header { position: absolute; left: 24px; top: 48px; }
  .front .photo-action {
    position: absolute; left: 0; top: 140px; width: 400px; height: 300px;
    background: linear-gradient(180deg, #6f96d8 0%, #a9c6ee 45%, #e6eefa 75%, #ffffff 100%);
  }
  .front .identity { position: absolute; left: 24px; top: 466px; }
  .person-name { font-size: 26px; font-weight: 700; color: var(--sky); letter-spacing: .5px; }
  .person-role { font-size: 17px; color: var(--white); margin-top: 2px; }
  .contacts { position: absolute; left: 24px; top: 544px; list-style: none; }
  .contacts li {
    display: flex; align-items: center; gap: 12px;
    font-size: 15px; color: var(--white); height: 24px; letter-spacing: .4px;
  }
  .contacts svg { width: 14px; height: 14px; flex: none; }
  .abn-row {
    position: absolute; left: 0; right: 0; top: 650px;
    display: flex; align-items: center; gap: 12px; padding: 0 14px;
  }
  .abn-row .rule { flex: 1; height: 1px; background: var(--muted); }
  .abn-row .abn { font-size: 16px; color: var(--white); letter-spacing: 1px; }
  /* back */
  .back .photo-wave {
    position: absolute; left: 0; top: 0; width: 400px; height: 270px;
    background: linear-gradient(180deg, #cfd6dc 0%, #eef1f3 55%, #6f8d8a 100%);
  }
  .back .band {
    position: absolute; left: 0; top: 270px; width: 400px; height: 150px;
    background: var(--navy-band);
    padding: 52px 0 0 24px;
  }
  .back .photo-start {
    position: absolute; left: 0; top: 420px; width: 400px; height: 280px;
    background: linear-gradient(180deg, #3a3336 0%, #8a6f6c 45%, #c9a79e 70%, #2c2a2d 100%);
  }
</style>
</head>
<body>
  <section class="card front" aria-label="Business card front">
    <header class="header">
      <div class="brand">Varnex Consulting</div>
      <div class="services">Search &amp; Select | Career | Coaching | Leadership | Outplacement</div>
    </header>
    <div class="photo-action" role="img" aria-label="Photo of a snowboarder mid-jump against a blue sky above a snowy peak"></div>
    <div class="identity">
      <div class="person-name">Gavin Threlkeld</div>
      <div class="person-role">Principal</div>
    </div>
    <ul class="contacts">
      <li>
        <svg viewBox="0 0 16 16" aria-hidden="true"><path fill="var(--muted)" d="M3 1.5l2.6 0 1 3.2-1.6 1.2a9 9 0 0 0 5 5l1.2-1.6 3.2 1v2.6c0 .8-.7 1.5-1.5 1.5A12 12 0 0 1 1.5 3c0-.8.7-1.5 1.5-1.5z"/></svg>
        1300 485 193
      </li>
      <li>
        <svg viewBox="0 0 16 16" aria-hidden="true"><rect x="1" y="3" width="14" height="10" fill="var(--muted)"/><path d="M1 3l7 6 7-6" fill="none" stroke="var(--navy)" stroke-width="1.3"/></svg>
        career@varnexconsulting.example
      </li>
      <li>
        <svg viewBox="0 0 16 16" aria-hidden="true"><path fill="var(--muted)" d="M8 1a5 5 0 0 1 5 5c0 3.5-5 9-5 9S3 9.5 3 6a5 5 0 0 1 5-5z"/><circle cx="8" cy="6" r="1.8" fill="var(--navy)"/></svg>
        PO Box 3172 Merrowdale NSW 2291
      </li>
    </ul>
    <div class="abn-row">
      <span class="rule"></span>
      <span class="abn">ABN: 71203948865</span>
      <span class="rule"></span>
    </div>
  </section>

  <section class="card back" aria-label="Business card back">
    <div class="photo-wave" role="img" aria-label="Photo of a surfer carving through white water"></div>
    <div class="band">
      <div class="brand">Varnex Consulting</div>
      <div class="services">Search &amp; Select | Career | Coaching | Leadership | Outplacement</div>
    </div>
    <div class="photo-start" role="img" aria-label="Photo of a sprinter's hands poised on the starting line of a track"></div>
  </section>
</body>
</html>
```